Postcard Design

The company is a global consulting company that is focusing on start-up business solutions and trade show management in the USA and overseas. The company web site is www.brimtolex.com.

We need the postcard to inform previous clients and industry contacts about our company.

We would like to see a design that includes the main colors of the logo, as well as the global consulting aspect.

The logo is attached.

Target Market(s)

Start-up business and trade shows element

Industry/Entity Type

Business

Requirements
Must have
• The logo needs to be included,

The international and start-up business ideas should be implemented.

```html
<!DOCTYPE html>
<html lang="en">
<head>
<meta charset="utf-8">
<title>Brimtolex Postcard</title>
<link rel="stylesheet" href="https://fonts.googleapis.com/css2?family=Open+Sans:wght@400;600;700&display=swap">
<style>
  :root {
    --blue-deep: #0b4c98;
    --blue-mid: #1f6fc0;
    --blue-light: #41a3e2;
    --blue-band: #2e86d3;
    --brand-blue: #17559f;
    --accent-orange: #e8822a;
    --white: #ffffff;
    --card-back: #f6f6f4;
    --line-grey: #9a9a9a;
    --stamp-grey: #8c8c8c;
    --text-dark: #111111;
    --border: #e2e2e2;
  }
  * { box-sizing: border-box; margin: 0; padding: 0; }
  html, body { width: 1200px; height: 473px; overflow: hidden; background: var(--white); }
  body { position: relative; font-family: "Open Sans", Arial, sans-serif; }

  .postcard-front, .postcard-back {
    position: absolute; top: 8px; width: 588px; height: 456px; overflow: hidden;
    border: 1px solid var(--border);
  }
  .postcard-front { left: 7px; }
  .postcard-back { left: 603px; background: var(--card-back); }

  .front-backdrop { position: absolute; inset: 0; width: 100%; height: 100%; }

  .tagline {
    position: absolute; left: 24px; top: 116px;
    color: var(--white); font-weight: 700; font-size: 19.5px; line-height: 27px; letter-spacing: 0.2px;
  }

  .front-brand {
    position: absolute; left: 300px; top: 268px; width: 240px;
    display: flex; align-items: center; justify-content: center; gap: 10px;
  }
  .brand-mark { width: 22px; height: 22px; background: var(--blue-light); flex: none; }
  .brand-name {
    color: var(--brand-blue); font-weight: 600; font-size: 40px; line-height: 1;
  }
  .front-slogan {
    position: absolute; left: 250px; top: 328px;
    color: var(--accent-orange); font-size: 12.2px; font-weight: 400; letter-spacing: 0.1px;
  }

  .back-brand {
    position: absolute; left: 15px; top: 13px; width: 134px; height: 134px;
    background: var(--white); box-shadow: 0 1px 4px rgba(0,0,0,0.25);
    display: flex; align-items: center; justify-content: center;
  }
  .back-brand .brand-name { font-size: 26px; }

  .stamp-box {
    position: absolute; left: 440px; top: 12px; width: 132px; height: 134px;
    border: 3px dotted var(--stamp-grey); background: var(--white);
    display: flex; align-items: center; justify-content: center; text-align: center;
    font-family: Arial, "Open Sans", sans-serif; font-size: 16px; line-height: 21px; color: var(--text-dark);
  }

  .divider {
    position: absolute; left: 282px; top: 147px; width: 1px; height: 230px; background: var(--line-grey);
  }
  .address-lines { position: absolute; left: 315px; top: 206px; width: 256px; list-style: none; }
  .address-lines li { height: 42px; border-bottom: 1px solid var(--line-grey); }
  .address-lines li:first-child { height: 1px; }
</style>
</head>
<body>
  <section class="postcard-front">
    <svg class="front-backdrop" viewBox="0 0 588 456" preserveAspectRatio="none" aria-hidden="true">
      <defs>
        <linearGradient id="frontBlue" x1="0" y1="0" x2="1" y2="1">
          <stop offset="0" stop-color="#45a8e4"/>
          <stop offset="0.45" stop-color="#1d6bbd"/>
          <stop offset="1" stop-color="#0a4892"/>
        </linearGradient>
      </defs>
      <rect width="588" height="456" fill="url(#frontBlue)"/>
      <path d="M420,0 C285,75 200,235 180,456 L212,456 C232,225 330,62 492,0 Z" fill="var(--blue-band)" opacity="0.85"/>
      <path d="M470,0 C320,70 225,230 205,456 L214,456 C234,226 334,62 500,0 Z" fill="#56b2ea"/>
      <path d="M500,0 C334,62 234,226 214,456 L588,456 L588,0 Z" fill="var(--white)"/>
    </svg>

    <p class="tagline">YOU HAVE AN IDEA.<br>WE HAVE A STRATEGY.</p>

    <div class="front-brand">
      <span class="brand-mark"></span>
      <span class="brand-name">Brimtolex</span>
    </div>
    <p class="front-slogan">YOUR GLOBAL SMALL BUSINESS CONSULTING TEAM</p>
  </section>

  <section class="postcard-back">
    <div class="back-brand"><span class="brand-name">Brimtolex</span></div>
    <div class="stamp-box">Place<br>Stamp<br>Here</div>
    <div class="divider"></div>
    <ul class="address-lines">
      <li></li><li></li><li></li><li></li><li></li>
    </ul>
  </section>
</body>
</html>
```